Layout of a white paper from an already written word document

We are a consulting company specializing in General Data Protection Regulation (GDPR) and cybersecurity. We wish to publish a white paper on our methodologies. The text is ready and we would like it to be laid out in a neat design.
Our target is SMEs and mid-caps.
We try to provide very concrete and pragmatic solutions to our clients. Attached is a sample white paper that we appreciate and the text to format.
Our web site: www.marlow-vantage.com
Target Market(s)
SMEs and mid-caps
Requirements
Must have
- A4 Format

```html
<!DOCTYPE html>
<html lang="fr">
<head>
<meta charset="utf-8">
<title>Modèle de maturité CDPA et Cyberattaques : 4 actions pour rassurer</title>
<link href="https://fonts.googleapis.com/css2?family=Pathway+Gothic+One&family=Open+Sans:wght@400;600;700&display=swap" rel="stylesheet">
<style>
  :root{
    --backdrop:#d4d4d4;
    --paper:#ffffff;
    --teal:#1aa3c8;
    --teal-deep:#1589ad;
    --navy:#1f3f8f;
    --ink:#2a2a2a;
    --muted:#6b6b6b;
    --tab:#f0b323;
    --rule:#9aa6c4;
    --flag:#f5c6c9;
    --flag-line:#d2313a;
    --soft-green:#dff0dc;
    --grade-a:#3aa655;
    --grade-b:#8cbf3f;
    --grade-c:#f0b323;
    --grade-d:#e67e22;
    --grade-f:#d2313a;
  }
  *{box-sizing:border-box;margin:0;padding:0}
  html,body{width:1200px;height:840px;overflow:hidden}
  body{background:var(--backdrop);position:relative;font-family:"Open Sans",Arial,sans-serif;color:var(--ink)}

  .sheet{position:absolute;background:var(--paper);display:flex;height:254px;box-shadow:0 0 0 .5px #c8c8c8}
  .sheet.single{width:180px}
  .sheet.spread{width:360px}
  .page{position:relative;width:180px;height:100%;padding:18px 14px 16px;overflow:hidden}
  .page::after{content:"";position:absolute;bottom:0;left:74px;width:32px;height:3px;background:var(--tab)}
  .folio{position:absolute;bottom:6px;left:0;right:0;text-align:center;font-size:2.6px;color:var(--muted)}

  .txt{font-size:2.9px;line-height:3.7px;text-align:justify;margin-bottom:2.6px;color:var(--ink)}
  .txt.lead{color:var(--teal);font-weight:600}
  .txt.quote{font-style:italic;padding-left:3px}
  .list{list-style:none;font-size:2.9px;line-height:3.9px;color:var(--teal);margin:1px 0 3px 6px;font-weight:600}
  .list.plain{color:var(--ink);font-weight:400;margin-left:3px;text-align:justify;line-height:3.7px}
  .list.plain li{margin-bottom:1.5px}
  .list.plain li::before{content:"■ ";color:var(--teal)}

  .h-section{font-family:"Pathway Gothic One",sans-serif;color:var(--teal);font-size:8.5px;line-height:9.5px;margin:3px 0 2px;font-weight:400}
  .h-action{font-family:"Pathway Gothic One",sans-serif;color:var(--teal);font-size:12px;line-height:13px;margin-bottom:2px;font-weight:400}
  .sub-action{font-size:3.4px;line-height:4.2px;color:var(--teal);margin-bottom:3px}

  .art{position:absolute;background:linear-gradient(135deg,#eaf4f8 0%,#9cc9dd 40%,#3f7fa6 70%,#f2a23a 100%);opacity:.9}

  /* cover */
  .cover-title{position:absolute;top:30px;right:14px;text-align:right;font-family:"Pathway Gothic One",sans-serif;color:var(--teal);font-size:13.5px;line-height:15px;font-weight:400}
  .cover-art{left:6px;right:6px;top:84px;bottom:6px;border-radius:2px;background:radial-gradient(ellipse at 55% 60%,#0e4f78 0%,#2e85b1 35%,#8fc3d9 62%,#eef6f9 80%,transparent 100%)}
  .brand{position:absolute;left:0;right:0;bottom:26px;display:flex;flex-direction:column;align-items:center;gap:2px;font-size:3.6px;font-weight:700;color:#ffffff;letter-spacing:.2px}
  .brand .dot{width:11px;height:11px;border-radius:50%;background:var(--tab)}

  /* contents spread */
  .band{position:absolute;left:0;right:0;top:122px;bottom:0;background:var(--teal)}
  .toc-head{position:absolute;left:28px;top:100px;font-family:"Pathway Gothic One",sans-serif;color:var(--teal);font-size:18px;font-weight:400}
  .toc{position:absolute;left:28px;right:14px;top:128px;font-size:3.1px;line-height:4.5px;color:#ffffff}
  .toc p{display:flex;justify-content:space-between;gap:6px;margin-bottom:4px}
  .toc p.main{font-weight:700}
  .on-band{position:absolute;left:14px;right:14px;top:128px;color:#ffffff}
  .on-band .txt{color:#ffffff}
  .num-item{display:flex;gap:3px;font-size:2.9px;line-height:3.7px;margin-bottom:3px;color:#ffffff;text-align:justify}
  .num-item b{font-size:8px;line-height:8px}

  /* maturity tables */
  .gt{border:.4px solid var(--rule);margin:3px 0 3px;position:relative;font-size:2.2px;line-height:2.8px}
  .gt-title{background:var(--navy);color:#fff;text-align:center;font-weight:700;font-size:2.9px;padding:1px 0}
  .gt-head,.gt-row{display:grid;grid-template-columns:1fr 1fr}
  .gt-head span{background:var(--teal-deep);color:#fff;text-align:center;padding:.6px 0;font-weight:600}
  .gt-row p{padding:1.5px 2px;border-right:.4px solid var(--rule);height:11px;overflow:hidden;color:var(--muted)}
  .gt-level{background:var(--teal-deep);color:#fff;text-align:center;font-weight:600;padding:.6px 0}
  .gt-steps,.gt-cells{display:grid;grid-template-columns:repeat(5,1fr)}
  .gt-steps span{border:.3px solid var(--rule);padding:1.2px;display:flex;align-items:center;gap:1.5px;font-weight:600;color:var(--ink);height:9px}
  .gt-steps span b{font-size:4px}
  .gt-steps span.hi{background:var(--teal-deep);color:#fff}
  .gt-cells p{border-right:.3px solid var(--rule);padding:1.5px;height:32px;overflow:hidden;color:var(--muted)}
  .gt-flag{position:absolute;width:34px;height:16px;border-radius:50%;background:var(--flag);border:.4px solid var(--flag-line);opacity:.85;bottom:5px;right:4px}
  .gt-ring{position:absolute;width:26px;height:26px;border-radius:50%;border:.4px dashed #4a9a52;background:var(--soft-green);opacity:.7;bottom:5px;left:40%}
  .gt-warn{position:absolute;bottom:3px;right:38px;width:0;height:0;border-left:4px solid transparent;border-right:4px solid transparent;border-bottom:7px solid var(--flag-line)}

  /* dashboards */
  .dash{border:.4px solid #cfd5de;background:#fbfcfd;margin:2px 0 3px;font-size:2.2px;line-height:2.8px;color:var(--muted)}
  .dash-top{display:flex;gap:4px;align-items:center;padding:2px 3px;border-bottom:.4px solid #dfe3ea;background:#f1f3f6}
  .dash-top b{color:var(--ink);font-size:2.8px}
  .dash-tab{padding:0 2px;border-bottom:.6px solid transparent}
  .dash-tab.on{border-color:var(--teal);color:var(--teal)}
  .dash-row{display:grid;grid-template-columns:9px 8px 1fr 18px 22px;align-items:center;gap:2px;padding:1.6px 3px;border-bottom:.3px solid #e4e8ee}
  .grade{width:6px;height:6px;border-radius:50%;border:.5px solid;display:flex;align-items:center;justify-content:center;font-weight:700;font-size:2.6px}
  .dash-row strong{display:block;color:var(--teal-deep);font-size:2.3px;font-weight:600}
  .dots{display:flex;gap:1px}
  .dots i{width:2.4px;height:2.4px;border-radius:50%;background:#d8dde5}
  .dots i.r{background:var(--grade-f)} .dots i.o{background:var(--grade-d)} .dots i.y{background:var(--grade-c)} .dots i.g{background:var(--grade-a)}
  .issue-grid{display:grid;grid-template-columns:repeat(4,1fr);gap:2px;padding:2px 3px}
  .issue-col p{border-bottom:.3px solid #e4e8ee;padding:.6px 0;white-space:nowrap;overflow:hidden}
  .issue-col p.h{color:#fff;padding:.6px 1px;font-weight:600}

  .doc-table{border:.4px solid var(--rule);margin:3px 0;font-size:2.2px;line-height:2.8px}
  .doc-table .bar{background:var(--navy);color:#fff;text-align:center;font-weight:700;padding:.8px 0;font-size:2.9px}
  .doc-table .row{display:grid;grid-template-columns:3fr 1fr 1.3fr 1.6fr;border-top:.3px solid var(--rule)}
  .doc-table .row p{padding:1px 1.5px;color:var(--muted);height:7.5px;overflow:hidden}
  .doc-table .row.head p{background:var(--teal-deep);color:#fff;height:auto}
</style>
</head>
<body>

<!-- Row 1 -->
<section class="sheet single" style="left:202px;top:26px">
  <div class="page" style="padding:0">
    <h1 class="cover-title">Modèle de maturité CDPA et<br>Cyberattaques :<br>4 actions pour rassurer</h1>
    <div class="art cover-art" role="img" aria-label="Illustration de facettes géométriques bleues et orangées évoquant la cybersécurité"></div>
    <div class="brand"><span class="dot"></span>MARLOW VANTAGE</div>
  </div>
</section>

<section class="sheet spread" style="left:431px;top:26px">
  <div class="band"></div>
  <div class="page">
    <div class="art" style="left:0;top:0;width:120px;height:70px;background:linear-gradient(135deg,#ffffff 0%,#a9d2e4 45%,#3d7ea4 75%,#f3a43a 100%)" role="img" aria-label="Éclats géométriques bleus et orangés"></div>
    <h2 class="toc-head">Contenu</h2>
    <div class="toc">
      <p class="main"><span>Modèle de maturité CDPA et Cyberattaques : 4 actions pour rassurer</span><span>3</span></p>
      <p><span>Première action : initier une nouvelle auto-évaluation avec le modèle de maturité publié par la CDPA</span><span>4</span></p>
      <p><span>Deuxième action : mettre en place des indicateurs objectifs en matière de sécurité</span><span>13</span></p>
      <p><span>Troisième action : mettre en place et faire vivre un dossier de conformité solide adapté aux spécificités de l'entreprise</span><span>16</span></p>
      <p><span>Quatrième action : mixer des compétences internes et externes pour garantir une réelle expertise</span><span>17</span></p>
    </div>
    <span class="folio" style="color:#fff">2</span>
  </div>
  <div class="page">
    <h2 class="h-action" style="font-size:9.5px;line-height:10px">Modèle de maturité CDPA et Cyberattaques : 4 actions pour rassurer</h2>
    <p class="sub-action" style="font-size:2.9px;line-height:3.6px">Dans un contexte post-crise très instable, face à des obligations réglementaires et des menaces inédites, les organisations ont besoin de consolider leurs activités auprès des clients, utilisateurs et investisseurs.</p>
    <p class="txt">En quelques mois, à cause et grâce à la crise, le marché a gagné en maturité et en expérience, ce qui a conduit les acteurs de la conformité et les régulateurs à se doter d'outils concrets. Le modèle publié récemment met à disposition une grille simple pour engager les équipes de façon pragmatique.</p>
    <p class="txt lead">Dans ce contexte, plusieurs constats permettent de comprendre l'urgence :</p>
    <ul class="list plain">
      <li>Depuis la crise, les audits internes se multiplient et les donneurs d'ordre exigent des preuves de sécurité.</li>
      <li>La concurrence entre sous-traitants n'a jamais été aussi forte : le niveau de conformité devient un critère d'achat.</li>
      <li>Les assureurs demandent des garanties mesurables avant de couvrir un risque cyber.</li>
    </ul>
    <div class="on-band">
      <p class="txt">Nous avons identifié ainsi quatre actions prioritaires pour rassurer efficacement clients, utilisateurs et investisseurs :</p>
      <div class="num-item"><b>1</b><span>Initier une nouvelle auto-évaluation avec le modèle de maturité publié par la CDPA, outil simple et reconnu.</span></div>
      <div class="num-item"><b>2</b><span>Mettre en place des indicateurs objectifs en matière de sécurité, en s'appuyant sur des outils de notation reconnus par le marché.</span></div>
      <div class="num-item"><b>3</b><span>Mettre en place et faire vivre un dossier de conformité adapté aux spécificités de l'entreprise, incluant les mesures utiles.</span></div>
      <div class="num-item"><b>4</b><span>Mixer les compétences internes et externes pour garantir une réelle expertise et protéger partenaires et clients.</span></div>
    </div>
    <span class="folio" style="color:#fff">3</span>
  </div>
</section>

<section class="sheet spread" style="left:814px;top:26px">
  <div class="page">
    <div class="art" style="left:0;top:0;width:110px;height:40px;background:linear-gradient(135deg,#ffffff 0%,#b8d8e6 50%,#5a93b5 100%)" role="img" aria-label="Éclats géométriques bleus"></div>
    <h2 class="h-action" style="margin-top:42px">Première action :</h2>
    <p class="sub-action">Initier une nouvelle auto-évaluation avec le modèle de maturité publié par la CDPA</p>
    <p class="txt">Le régulateur a partagé ses premières réflexions sur la réalisation d'un modèle de maturité en gestion de la protection des données. Le projet décrit huit activités liées à la protection des données et cinq niveaux de maturité.</p>
    <p class="txt">Nous avons testé ce modèle avec nos clients : il permet de structurer les missions du délégué et de clarifier les rôles de chacun. La méthode propose six niveaux :</p>
    <ul class="list"><li>0. Pratique inexistante ou incomplète</li><li>1. Pratique informelle</li><li>2. Pratique répétable et suivie</li><li>3. Processus défini</li><li>4. Processus contrôlé</li><li>5. Processus continuellement optimisé</li></ul>
    <p class="txt">Chaque niveau évalue la manière dont une organisation conçoit, met en œuvre et contrôle sa pratique. Le niveau trois est facilement atteint ; les niveaux supérieurs demandent implication et ressources.</p>
    <p class="txt">Pour mieux appréhender l'intérêt opérationnel de ce modèle, nous avons réalisé une évaluation avec les responsables de traitement de plusieurs entreprises.</p>
    <p class="txt lead">Leurs commentaires sont les suivants :</p>
    <p class="txt quote">« Il est précieux pour les dirigeants de s'appuyer sur un référentiel officiel pour structurer leur démarche et mesurer les progrès accomplis. »</p>
    <span class="folio">4</span>
  </div>
  <div class="page">
    <div class="art" style="right:0;top:0;width:60px;height:28px;background:linear-gradient(225deg,#ffffff 0%,#a9cfe1 55%,#3d7ea4 100%)" role="img" aria-label="Éclats géométriques bleus"></div>
    <p class="txt quote" style="margin-top:22px">« Il permet de mieux cerner les attentes du régulateur et d'être prêt en cas de contrôle ou de réponse à un client. Il sensibilise les équipes aux enjeux internes et externes. »</p>
    <p class="txt quote">« Il est une invitation au progrès : l'entreprise doit fournir à ses clients des preuves concrètes et viser au minimum le niveau trois. »</p>
    <div class="gt">
      <div class="gt-title">Autoévaluation selon la Méthode de Maturité</div>
      <div class="gt-head"><span>Niveau</span><span>Caractéristiques</span></div>
      <div class="gt-cells" style="grid-template-columns:1fr 3fr"><p style="height:66px">0 Inexistante<br><br>1 Informelle<br><br>2 Répétable et suivie<br><br>3 Processus défini<br><br>4 Processus contrôlé<br><br>5 Optimisé</p><p style="height:66px">Aucune pratique formalisée, actions menées au cas par cas.<br><br>Actions isolées, dépendantes de quelques personnes clés.<br><br>Pratiques répétées, suivies et connues des équipes.<br><br>Processus documenté, partagé et appliqué par tous.<br><br>Mesures quantitatives et correction des défauts constatés.<br><br>Amélioration continue pilotée par des indicateurs.</p></div>
      <div class="gt-ring" style="left:10px;bottom:18px"></div>
    </div>
    <p class="txt">L'utilisation de cette méthode est utile dans un contexte d'incertitude : elle aide à prioriser les efforts, à justifier les budgets et à dialoguer avec la direction.</p>
    <p class="txt">Elle permet aussi de répondre aux questionnaires des grands comptes et de démontrer une trajectoire d'amélioration réaliste, adaptée à la taille de l'entreprise.</p>
    <p class="txt">Enfin, elle facilite le choix des actions prioritaires en s'appuyant sur un langage commun à toutes les directions.</p>
    <span class="folio">5</span>
  </div>
</section>

<!-- Row 2 -->
<section class="sheet spread" style="left:22px;top:293px">
  <div class="page">
    <p class="txt">Le DPO et la Direction Juridique vont donc enfin disposer de l'outil d'animation pour l'exercice de leurs missions, qui leur permettra de renforcer leur crédibilité auprès des métiers :</p>
    <ul class="list"><li>1. Définir et mettre en œuvre des procédures</li><li>2. Piloter la gouvernance</li><li>3. Recenser et tenir à jour les traitements</li><li>4. Assurer la conformité juridique</li><li>5. Former et sensibiliser</li><li>6. Traiter les demandes des usagers</li><li>7. Gérer les risques de sécurité</li><li>8. Gérer les violations de données</li></ul>
    <p class="txt">Pour chacune de ces activités sont précisées les caractéristiques, les responsables impliqués et des exemples concrets de niveau de maturité.</p>
    <h3 class="h-section">1. Définir et mettre en œuvre des procédures de protection des données</h3>
    <p class="txt">La formalisation des procédures est à la portée de tous ; leur application demande un suivi régulier et une réelle implication des équipes opérationnelles.</p>
    <div class="gt">
      <div class="gt-title">1/ Définir et mettre en œuvre des procédures</div>
      <div class="gt-head"><span>Caractéristiques</span><span>Responsables impliqués</span></div>
      <div class="gt-row"><p>Politiques, règles et procédures documentées, diffusées et appliquées.</p><p>DPO, direction juridique, responsables métiers.</p></div>
      <div class="gt-level">Niveau de maturité</div>
      <div class="gt-steps"><span><b>1</b>Informelle</span><span><b>2</b>Répétable</span><span><b>3</b>Définie</span><span><b>4</b>Contrôlée</span><span class="hi"><b>5</b>Optimisée</span></div>
      <div class="gt-cells"><p>Quelques règles éparses, non écrites.</p><p>Procédures connues des équipes.</p><p>Documentation partagée et à jour.</p><p>Contrôles réguliers de l'application.</p><p>Revue continue et améliorations.</p></div>
      <div class="gt-ring"></div><div class="gt-flag"></div><div class="gt-warn"></div>
    </div>
    <p class="txt">Il ne s'agit pas simplement de documenter, il faut réussir à faire vivre la conformité.</p>
    <span class="folio">6</span>
  </div>
  <div class="page">
    <p class="txt">Les efforts se font depuis l'entrée en application du règlement en regroupant la documentation dans un dossier unique, facilement accessible par les personnes habilitées. Néanmoins, la publication du modèle rend la conformité plus lisible et les compléments utiles.</p>
    <h3 class="h-section">2. Piloter la gouvernance de la protection des données</h3>
    <p class="txt">Un pilotage de la gouvernance sous-entend qu'il implique les différents responsables de l'organisation. Ce pilotage est de manière générale assuré par le DPO, avec la mise en place d'un comité et d'une feuille de route partagée.</p>
    <div class="gt">
      <div class="gt-title">2/ Piloter la gouvernance</div>
      <div class="gt-head"><span>Caractéristiques</span><span>Responsables impliqués</span></div>
      <div class="gt-row"><p>Stratégie, feuille de route et instances de pilotage définies.</p><p>Direction générale, DPO, RSSI.</p></div>
      <div class="gt-level">Niveau de maturité</div>
      <div class="gt-steps"><span><b>1</b>Informelle</span><span><b>2</b>Répétable</span><span><b>3</b>Définie</span><span><b>4</b>Contrôlée</span><span class="hi"><b>5</b>Optimisée</span></div>
      <div class="gt-cells"><p>Aucun comité ni suivi formalisé.</p><p>Points ponctuels avec la direction.</p><p>Comité identifié et réuni.</p><p>Indicateurs suivis et partagés.</p><p>Amélioration pilotée et budgétée.</p></div>
      <div class="gt-ring"></div><div class="gt-flag"></div><div class="gt-warn"></div>
    </div>
    <p class="txt">Un bon pilotage de la gouvernance est efficace : il permet l'existence de processus à jour, optimisés ou à minima contrôlés. L'évaluation de chaque activité est l'occasion d'un échange pédagogique avec les directions et crédibilise le DPO.</p>
    <p class="txt">Lors des périodes de négociation budgétaire, la crédibilité du DPO est essentielle, car même si celui-ci peut s'appuyer sur des collaborateurs, il reste le garant du dispositif.</p>
    <span class="folio">7</span>
  </div>
</section>

<section class="sheet spread" style="left:431px;top:293px">
  <div class="page">
    <h3 class="h-section">3. Recenser et tenir à jour la liste des traitements</h3>
    <p class="txt">Comme l'indique le régulateur, le registre sert d'instrument de pilotage des actions relatives aux traitements de données personnelles. Il permet de cartographier les données et de révéler les points d'amélioration.</p>
    <div class="gt">
      <div class="gt-title">3/ Recenser et tenir à jour la liste des traitements</div>
      <div class="gt-head"><span>Caractéristiques</span><span>Responsables impliqués</span></div>
      <div class="gt-row"><p>Registre complet, structuré et mis à jour à chaque projet.</p><p>Métiers, DPO, DSI.</p></div>
      <div class="gt-level">Niveau de maturité</div>
      <div class="gt-steps"><span><b>1</b>Informelle</span><span><b>2</b>Répétable</span><span><b>3</b>Définie</span><span><b>4</b>Contrôlée</span><span class="hi"><b>5</b>Optimisée</span></div>
      <div class="gt-cells"><p>Liste partielle et ancienne.</p><p>Tableur commun aux équipes.</p><p>Registre structuré et complet.</p><p>Mises à jour suivies et datées.</p><p>Outil intégré aux projets.</p></div>
      <div class="gt-flag" style="right:40px"></div><div class="gt-warn" style="right:30px"></div>
    </div>
    <p class="txt">Qu'il soit généré par un outil spécialisé ou à partir d'un tableur, un registre mal tenu devient vite inutile. Un outil spécialisé évite les limites d'un tableur partagé et rend le registre plus lisible.</p>
    <p class="txt">Le modèle de registre publié par le régulateur reste une bonne base de départ, plus lisible et plus simple à alimenter pour les PME.</p>
    <p class="txt">Il doit être revu à chaque nouveau projet, changement de prestataire ou évolution d'un outil métier.</p>
    <span class="folio">8</span>
  </div>
  <div class="page">
    <h3 class="h-section">4. Assurer la conformité juridique des traitements</h3>
    <p class="txt">Certains ne l'ont pas encore intégré, mais la protection des données doit être pensée dès la conception du projet, avec l'appui du DPO et de la direction juridique. L'analyse d'impact est obligatoire pour les traitements à risque élevé.</p>
    <div class="gt">
      <div class="gt-title">4/ Assurer la conformité juridique des traitements</div>
      <div class="gt-head"><span>Caractéristiques</span><span>Responsables impliqués</span></div>
      <div class="gt-row"><p>Analyses d'impact, bases légales et contrats vérifiés.</p><p>Juridique, métiers, DPO.</p></div>
      <div class="gt-level">Niveau de maturité</div>
      <div class="gt-steps"><span><b>1</b>Informelle</span><span><b>2</b>Répétable</span><span><b>3</b>Définie</span><span><b>4</b>Contrôlée</span><span class="hi"><b>5</b>Optimisée</span></div>
      <div class="gt-cells"><p>Avis au cas par cas.</p><p>Modèles de clauses diffusés.</p><p>Analyses menées sur les projets.</p><p>Contrôle des projets en amont.</p><p>Veille continue et partagée.</p></div>
      <div class="gt-flag" style="right:60px"></div><div class="gt-warn" style="right:52px"></div>
    </div>
    <p class="txt">Pour beaucoup de dirigeants, l'analyse d'impact est un sujet de friction et de coûts difficile à accepter. Les ressources internes de l'entreprise n'ont pas l'habitude de l'exercice.</p>
    <p class="txt">Elle reste pourtant un levier de confiance : elle permet de mandater un prestataire en connaissance de cause et de prévoir un budget pour la mise en œuvre des mesures correctives.</p>
    <span class="folio">9</span>
  </div>
</section>

<section class="sheet spread" style="left:814px;top:293px">
  <div class="page">
    <h3 class="h-section">5. Former et sensibiliser</h3>
    <p class="txt">C'est un sujet simple que l'on ne peut ignorer : la formation reste la première barrière face aux attaques et aux erreurs humaines.</p>
    <div class="gt">
      <div class="gt-title">5/ Former et sensibiliser</div>
      <div class="gt-level">Niveau de maturité</div>
      <div class="gt-steps"><span><b>1</b>Informelle</span><span><b>2</b>Répétable</span><span><b>3</b>Définie</span><span><b>4</b>Contrôlée</span><span class="hi"><b>5</b>Optimisée</span></div>
      <div class="gt-cells"><p>Rien de planifié.</p><p>Rappels ponctuels.</p><p>Plan annuel suivi.</p><p>Quiz et mesures.</p><p>Culture partagée.</p></div>
      <div class="gt-ring" style="left:30%"></div>
    </div>
    <p class="txt">La diffusion de la connaissance et la création de compétences internes sont des leviers durables.</p>
    <h3 class="h-section">6. Traiter les demandes des usagers internes et externes</h3>
    <p class="txt">La plupart des sanctions prononcées font suite à des plaintes d'usagers dont la demande n'a pas été traitée dans les délais.</p>
    <div class="gt">
      <div class="gt-title">6/ Traiter les demandes des usagers</div>
      <div class="gt-level">Niveau de maturité</div>
      <div class="gt-steps"><span><b>1</b>Informelle</span><span><b>2</b>Répétable</span><span><b>3</b>Définie</span><span><b>4</b>Contrôlée</span><span class="hi"><b>5</b>Optimisée</span></div>
      <div class="gt-cells"><p>Réponses tardives.</p><p>Boîte dédiée.</p><p>Délais suivis.</p><p>Tableau de bord.</p><p>Portail usager.</p></div>
      <div class="gt-flag" style="left:30px;right:auto"></div>
    </div>
    <span class="folio">10</span>
  </div>
  <div class="page">
    <p class="txt">Les demandes d'exercice de droits sont souvent le premier signal d'un litige avec un usager ; un traitement rapide évite qu'il ne se transforme en plainte.</p>
    <h3 class="h-section">7. Gérer les risques de sécurité</h3>
    <p class="txt">Bon nombre de sinistres cyber analysés par les compagnies d'assurance ont fait apparaître des lacunes en matière de sécurité des données et des prestataires. L'appréciation des risques doit couvrir l'ensemble des traitements et des sous-traitants.</p>
    <div class="gt">
      <div class="gt-title">7/ Gérer les risques de sécurité</div>
      <div class="gt-head"><span>Caractéristiques</span><span>Responsables impliqués</span></div>
      <div class="gt-row"><p>Risques identifiés, évalués et traités par des mesures adaptées.</p><p>RSSI, DSI, DPO.</p></div>
      <div class="gt-level">Niveau de maturité</div>
      <div class="gt-steps"><span><b>1</b>Informelle</span><span><b>2</b>Répétable</span><span><b>3</b>Définie</span><span><b>4</b>Contrôlée</span><span class="hi"><b>5</b>Optimisée</span></div>
      <div class="gt-cells"><p>Mesures isolées.</p><p>Inventaire connu.</p><p>Analyse menée.</p><p>Suivi des écarts.</p><p>Notation externe.</p></div>
      <div class="gt-flag"></div><div class="gt-warn"></div>
    </div>
    <p class="txt">Comme nous le verrons dans la deuxième action, la mise en place d'indicateurs objectifs de sécurité, en s'appuyant sur des outils de notation par une tierce partie, permet de disposer d'une veille sur les vulnérabilités et de prioriser les actions correctives.</p>
    <span class="folio">11</span>
  </div>
</section>

<!-- Row 3 -->
<section class="sheet spread" style="left:22px;top:561px">
  <div class="page">
    <h3 class="h-section">8. Gérer les violations de données</h3>
    <p class="txt">Cette dernière activité est la suite logique de la précédente. L'appréciation des risques de sécurité permet de limiter les incidents, mais chaque violation doit être tracée, analysée et, si nécessaire, notifiée dans les délais.</p>
    <div class="gt">
      <div class="gt-title">8/ Gérer les violations de données</div>
      <div class="gt-head"><span>Caractéristiques</span><span>Responsables impliqués</span></div>
      <div class="gt-row"><p>Procédure de notification documentée et testée.</p><p>RSSI, DPO, direction.</p></div>
      <div class="gt-level">Niveau de maturité</div>
      <div class="gt-steps"><span><b>1</b>Informelle</span><span><b>2</b>Répétable</span><span><b>3</b>Définie</span><span><b>4</b>Contrôlée</span><span class="hi"><b>5</b>Optimisée</span></div>
      <div class="gt-cells"><p>Gestion improvisée.</p><p>Contacts connus.</p><p>Registre des incidents.</p><p>Exercices annuels.</p><p>Retour d'expérience.</p></div>
      <div class="gt-ring" style="left:20%"></div><div class="gt-flag" style="right:50px"></div><div class="gt-warn" style="right:40px"></div>
    </div>
    <p class="txt">Cette activité est souvent la moins maîtrisée dans les organisations. Il est rare que les équipes aient déjà vécu une crise ; un exercice de simulation annuel change profondément leur capacité de réaction.</p>
    <p class="txt">Comme expliqué dans notre quatrième action, le responsable de traitement peut se faire accompagner par un expert externe pour atteindre le niveau quatre.</p>
    <span class="folio">12</span>
  </div>
  <div class="page">
    <h2 class="h-action">Deuxième action :</h2>
    <p class="sub-action">Mettre en place des indicateurs objectifs en matière de sécurité, en s'appuyant sur des outils de notation comme RiskGauge ou ScoreHarbor</p>
    <p class="txt">Le modèle de maturité ne suffit pas : il faut disposer d'indicateurs objectifs pour évaluer le niveau de sécurité de l'entreprise. Depuis la crise, la cybermenace croît de manière exponentielle, avec un nombre record de signalements auprès des autorités.</p>
    <p class="txt">La montée des rançongiciels s'explique par la facilité d'attaquer des systèmes mal protégés, et les petites entreprises sont devenues des cibles privilégiées.</p>
    <p class="txt">La densité de l'actualité sur ce sujet au cours des derniers mois confirme la croissance continue du phénomène :</p>
    <ul class="list plain"><li>Des serveurs de messagerie ont été visés par des attaques massives touchant des milliers d'organisations.</li><li>Un fichier contenant des millions d'identifiants a été publié en ligne.</li><li>Plusieurs hôpitaux ont subi des interruptions de service prolongées.</li></ul>
    <p class="txt">Les entreprises de moins de cinquante salariés sont particulièrement exposées : un incident majeur peut menacer leur survie en quelques semaines.</p>
    <p class="txt">Le recours à des outils tiers objectifs devient un moyen convaincant de démontrer son niveau de maturité. Ces plateformes notent la sécurité à partir d'informations publiques, sans installation chez le client.</p>
    <span class="folio">13</span>
  </div>
</section>

<section class="sheet spread" style="left:431px;top:561px">
  <div class="page">
    <p class="txt">Le tableau de bord principal qui apparaît en premier lieu permet de disposer d'une évaluation globale et détaillée par domaine de vulnérabilité. Les niveaux d'évaluation sont A, B, C, D et F.</p>
    <div class="dash">
      <div class="dash-top"><b>Vue d'ensemble</b><span class="dash-tab on">Domaines</span><span class="dash-tab">Problèmes</span><span class="dash-tab">Historique</span><span class="dash-tab">Rapports</span></div>
      <div class="dash-row"><span class="grade" style="color:var(--grade-f)">F</span><span>55</span><span><strong>Sécurité réseau</strong>Ports ouverts, services exposés</span><span>3 constats</span><span class="dots"><i class="r"></i><i class="o"></i><i class="y"></i><i></i><i></i></span></div>
      <div class="dash-row"><span class="grade" style="color:var(--grade-d)">D</span><span>68</span><span><strong>Santé DNS</strong>Configuration des domaines</span><span>2 constats</span><span class="dots"><i class="o"></i><i class="y"></i><i></i><i></i><i></i></span></div>
      <div class="dash-row"><span class="grade" style="color:var(--grade-a)">A</span><span>100</span><span><strong>Cadence des correctifs</strong>Mises à jour appliquées</span><span>0 constat</span><span class="dots"><i class="g"></i><i class="g"></i><i></i><i></i><i></i></span></div>
      <div class="dash-row"><span class="grade" style="color:var(--grade-b)">B</span><span>86</span><span><strong>Sécurité des postes</strong>Navigateurs et systèmes</span><span>1 constat</span><span class="dots"><i class="y"></i><i class="g"></i><i></i><i></i><i></i></span></div>
      <div class="dash-row"><span class="grade" style="color:var(--grade-c)">C</span><span>74</span><span><strong>Signaux IP</strong>Activité suspecte observée</span><span>2 constats</span><span class="dots"><i class="o"></i><i class="y"></i><i class="y"></i><i></i><i></i></span></div>
      <div class="dash-row"><span class="grade" style="color:var(--grade-a)">A</span><span>98</span><span><strong>Sécurité applicative</strong>Sites et formulaires web</span><span>0 constat</span><span class="dots"><i class="g"></i><i></i><i></i><i></i><i></i></span></div>
      <div class="dash-row"><span class="grade" style="color:var(--grade-b)">B</span><span>88</span><span><strong>Bavardage pirate</strong>Mentions sur les forums</span><span>1 constat</span><span class="dots"><i class="y"></i><i class="g"></i><i></i><i></i><i></i></span></div>
      <div class="dash-row"><span class="grade" style="color:var(--grade-a)">A</span><span>100</span><span><strong>Fuites d'informations</strong>Identifiants exposés</span><span>0 constat</span><span class="dots"><i class="g"></i><i></i><i></i><i></i><i></i></span></div>
      <div class="dash-row"><span class="grade" style="color:var(--grade-c)">C</span><span>72</span><span><strong>Ingénierie sociale</strong>Exposition des employés</span><span>2 constats</span><span class="dots"><i class="o"></i><i class="y"></i><i></i><i></i><i></i></span></div>
      <div class="dash-row" style="border-bottom:0"><span class="grade" style="color:var(--grade-b)">B</span><span>84</span><span><strong>Réputation IP</strong>Listes de blocage</span><span>1 constat</span><span class="dots"><i class="y"></i><i></i><i></i><i></i><i></i></span></div>
    </div>
    <p class="txt">Les compagnies d'assurance jugent qu'une entreprise est viable si elle a une note globale de A ou B. Au-delà, elles refusent dans certains cas de contracter avec elle ou augmentent fortement la prime.</p>
    <span class="folio">14</span>
  </div>
  <div class="page">
    <p class="txt">Un tableau des anomalies détectées pour chaque domaine de vulnérabilité est disponible et oriente les équipes techniques vers les corrections à mener en priorité.</p>
    <div class="dash">
      <div class="dash-top"><b>Sécurité réseau</b><span>Note 55 · F</span></div>
      <div class="issue-grid">
        <div class="issue-col"><p class="h" style="background:var(--grade-f)">Élevé</p><p>Port distant exposé</p><p>Base ouverte</p><p>Service obsolète</p></div>
        <div class="issue-col"><p class="h" style="background:var(--grade-d)">Moyen</p><p>Certificat expiré</p><p>Protocole faible</p><p>Accès non chiffré</p></div>
        <div class="issue-col"><p class="h" style="background:var(--grade-c)">Faible</p><p>En-tête manquant</p><p>Bannière visible</p><p>Cookie non sécurisé</p></div>
        <div class="issue-col"><p class="h" style="background:var(--grade-a)">Positif</p><p>Pare-feu actif</p><p>Chiffrement à jour</p><p>Correctifs appliqués</p></div>
      </div>
    </div>
    <p class="txt">Au fur et à mesure que les anomalies sont corrigées, il est possible d'en informer la plateforme qui réévalue la note et en retrace l'évolution dans le temps.</p>
    <div class="dash">
      <div class="dash-top"><b>Historique de la note</b><span class="dash-tab on">12 mois</span><span class="dash-tab">Secteur</span></div>
      <svg viewBox="0 0 150 48" width="100%" height="48" role="img" aria-label="Courbe d'évolution de la note de sécurité sur douze mois">
        <g stroke="#e4e8ee" stroke-width=".3"><line x1="10" y1="8" x2="146" y2="8"/><line x1="10" y1="20" x2="146" y2="20"/><line x1="10" y1="32" x2="146" y2="32"/><line x1="10" y1="42" x2="146" y2="42"/></g>
        <g font-size="2.4" fill="#6b6b6b"><text x="2" y="9">A</text><text x="2" y="21">B</text><text x="2" y="33">C</text><text x="2" y="43">D</text></g>
        <polyline fill="none" stroke="#d2313a" stroke-width=".7" points="12,40 24,39 36,38 48,36 60,33 72,30 84,27 96,22 108,18 120,15 132,12 144,10"/>
        <polyline fill="none" stroke="#1589ad" stroke-width=".5" stroke-dasharray="1.5 1" points="12,24 24,24 36,23 48,23 60,22 72,22 84,22 96,21 108,21 120,21 132,20 144,20"/>
      </svg>
    </div>
    <p class="txt">Si la certification reste un bon outil pour crédibiliser le niveau de sécurité, elle est plus lourde à mettre en œuvre pour les PME. La notation externe est alors un complément rapide, lisible par les clients et les investisseurs.</p>
    <span class="folio">15</span>
  </div>
</section>

<section class="sheet spread" style="left:814px;top:561px">
  <div class="page">
    <h2 class="h-action">Troisième action :</h2>
    <p class="sub-action">Mettre en place et faire vivre un dossier de conformité solide adapté aux spécificités de l'entreprise</p>
    <p class="txt">La mise en conformité et sa gestion quotidienne imposent à l'organisation le déploiement de mesures appropriées, et une documentation actualisée, accessible et démontrable en cas de contrôle. Le dossier s'organise en cinq thèmes :</p>
    <ul class="list plain"><li>Les fondamentaux de la conformité</li><li>Transparence et information des personnes</li><li>Sécurité, intégrité et confidentialité</li><li>Aspects contractuels et sous-traitance</li></ul>
    <div class="doc-table">
      <div class="bar">Document d'évaluation des mesures de conformité</div>
      <div class="row head"><p>Mesures</p><p>Date</p><p>Avis DPO</p><p>Justificatifs</p></div>
      <div class="row"><p>Procédures documentées et diffusées</p><p>09/2021</p><p>Validé</p><p>Charte interne</p></div>
      <div class="row"><p>Registre des traitements à jour</p><p>09/2021</p><p>Validé</p><p>Registre</p></div>
      <div class="row"><p>Information des personnes concernées</p><p>10/2021</p><p>En cours</p><p>Mentions légales</p></div>
      <div class="row"><p>Gestion des incidents et violations</p><p>10/2021</p><p>En cours</p><p>Procédure</p></div>
      <div class="row"><p>Contrats avec les sous-traitants</p><p>11/2021</p><p>À revoir</p><p>Avenants</p></div>
    </div>
    <p class="txt">Pour chacune des mesures, le document mentionne la date d'évaluation, l'avis du DPO et les justificatifs associés. Les liens vers les preuves permettent de disposer instantanément des éléments utiles dans le cadre d'un audit client.</p>
    <span class="folio">16</span>
  </div>
  <div class="page">
    <h2 class="h-action">Quatrième action :</h2>
    <p class="sub-action">Mixer des compétences internes (savoir-faire métier) et externes pour garantir une réelle expertise et protéger vos partenaires</p>
    <p class="txt">Les entreprises de taille intermédiaire ont souvent un responsable dédié à la conformité ; les PME s'appuient plutôt sur des ressources partagées entre plusieurs fonctions, ce qui limite le temps consacré au sujet.</p>
    <p class="txt">Il convient d'identifier les différentes expertises nécessaires à la gestion de la conformité et de la sécurité. Elles peuvent être regroupées en trois catégories :</p>
    <ul class="list plain"><li>Les savoirs organisationnels : conduite du changement, gestion de projet et animation des équipes métiers.</li><li>Les savoirs techniques : sécurité des systèmes, des réseaux et des applications de l'entreprise.</li><li>Les savoirs juridiques : contrats, droits des personnes et veille réglementaire.</li></ul>
    <p class="txt">On notera enfin que les savoirs techniques, informatiques et juridiques liés au règlement sont des domaines particulièrement exigeants.</p>
    <p class="txt">Un DPO externalisé apporte un regard neutre et une expertise mutualisée, tout en restant proche des équipes. Il s'appuie sur les référents internes qui connaissent les métiers et les processus.</p>
    <p class="txt">Cette combinaison rassure durablement clients, assureurs et investisseurs, pour un coût maîtrisé.</p>
    <span class="folio">17</span>
  </div>
</section>

</body>
</html>
```